Corvane Holdings , new business card design

investment firm with corporate clients . need double sided business card , vertical and horizontal options ,logo must be clear. prefer pantone colors only and sharp design. website also www.corvane.ae

Khalid Bin Tarrafi
Managing Director
Tel. +971 4 387 2940
Mobile +971 50 518 2403
khalid@corvane.ae
Q-Span Plaza, officw 18-B07, Warqa Gardens, Dubai

Contact Information for Business Card

Khalid Bin Tarrafi
Managing Director

Font styles to use
Serif

Colors

Designer to choose colors to be used in the design.

```html
<!DOCTYPE html>
<html lang="en">
<head>
<meta charset="utf-8">
<title>Corvane Holdings — Business Card</title>
<link rel="stylesheet" href="https://fonts.googleapis.com/css2?family=Questrial&family=Montserrat:wght@700&display=swap">
<style>
  :root {
    --stage: #1d1d1f;
    --brand-blue: #44709b;
    --card-white: #eeeeee;
    --ink: #2b2b2b;
    --rule: #b9b9b9;
    --on-blue: #ffffff;
  }
  * { margin: 0; padding: 0; box-sizing: border-box; }
  html, body { width: 1200px; height: 900px; overflow: hidden; }
  body {
    background: var(--stage);
    font-family: "Questrial", "Century Gothic", sans-serif;
    color: var(--ink);
    position: relative;
  }
  .card {
    position: absolute;
    left: 330px;
    width: 540px;
    height: 310px;
    border-radius: 22px;
    overflow: hidden;
  }
  .card--back { top: 115px; background: var(--brand-blue); color: var(--on-blue); }
  .card--front { top: 475px; background: var(--card-white); }

  .wordmark {
    font-family: "Questrial", "Century Gothic", sans-serif;
    text-transform: uppercase;
    white-space: nowrap;
  }
  .card--back .wordmark {
    position: absolute; left: 40px; right: 40px; top: 118px;
    text-align: center; font-size: 28px; letter-spacing: 8px;
    text-indent: 8px;
    color: var(--on-blue);
  }
  .card--back .website {
    position: absolute; left: 0; right: 0; top: 180px;
    text-align: center; font-size: 14px; letter-spacing: 3px;
    text-indent: 3px;
  }

  .card--front .wordmark {
    position: absolute; right: 36px; top: 44px;
    font-size: 22px; letter-spacing: 6px; margin-right: -6px;
    color: var(--ink);
  }
  .card--front .top-rule {
    position: absolute; left: 250px; right: 36px; top: 98px;
    border-top: 1px solid var(--rule);
  }
  .holder { position: absolute; left: 36px; top: 148px; }
  .holder__name {
    font-family: "Montserrat", sans-serif; font-weight: 700;
    font-size: 17px; color: var(--brand-blue); text-transform: uppercase;
  }
  .holder__title { font-size: 15px; margin-top: 1px; }
  .holder__rule {
    position: absolute; left: 36px; width: 230px; top: 201px;
    border-top: 1px solid var(--rule);
  }
  .contacts { position: absolute; left: 36px; top: 210px; list-style: none; }
  .contacts li {
    display: flex; align-items: center; gap: 9px;
    font-size: 15px; line-height: 21px;
  }
  .contacts svg { width: 13px; height: 13px; fill: var(--brand-blue); flex: none; }
  .address {
    position: absolute; right: 36px; top: 148px;
    text-align: right; font-size: 15px; line-height: 21px;
  }
</style>
</head>
<body>
  <section class="card card--back" aria-label="Card back">
    <p class="wordmark">Corvane Holdings</p>
    <p class="website">www.corvane.ae</p>
  </section>

  <section class="card card--front" aria-label="Card front">
    <p class="wordmark">Corvane Holdings</p>
    <div class="top-rule"></div>

    <div class="holder">
      <p class="holder__name">Khalid Bin Tarrafi</p>
      <p class="holder__title">Managing Director</p>
    </div>
    <div class="holder__rule"></div>

    <ul class="contacts">
      <li>
        <svg viewBox="0 0 16 16" aria-hidden="true"><path d="M2 6c0-2 2-3 6-3s6 1 6 3v1h-3V5.5H5V7H2zM3 8h10l1 6H2z"/></svg>
        +971 4 387 2940
      </li>
      <li>
        <svg viewBox="0 0 16 16" aria-hidden="true"><path d="M4 0h8a1 1 0 0 1 1 1v14a1 1 0 0 1-1 1H4a1 1 0 0 1-1-1V1a1 1 0 0 1 1-1zm1 2v10h6V2zm3 11a1 1 0 1 0 0 2 1 1 0 0 0 0-2z"/></svg>
        +971 50 518 2403
      </li>
      <li>
        <svg viewBox="0 0 16 16" aria-hidden="true"><path d="M0 3h16v10H0zm1.5 1.2L8 9l6.5-4.8V4h-13z"/></svg>
        khalid@corvane.ae
      </li>
      <li>
        <svg viewBox="0 0 16 16" aria-hidden="true"><circle cx="8" cy="8" r="7.5"/></svg>
        www.corvane.ae
      </li>
    </ul>

    <p class="address">Q-Span Plaza, officw 18-B07<br>Warqa Gardens, Dubai</p>
  </section>
</body>
</html>
```